Sassy, natural personal lubricant knows that it is not always about the packaging

An opportunity exists to create packaging for the world's first Macadamia Oil personal lubricant - Warrabee Silk. Unlike any other personal lubricants, this product is created from pure macadamia nut oil. The fatty acids naturally occurring in Macadamia oil are highly anti-inflammatory and are the closest in composition to human skin lipids. Using Warrabee Silk in such a vulnerable part of our bodies is the safest and gentlest way to enhance sexual enjoyment while moisturizing and adding lubrication. Warrabee Silk is completely free of the parabens, glycerins, fragrances, hormones, silicones and petroleum products known to irritate the delicate vaginal wall.

Design tone for Warrabee Silk:
- intelligent, but not condescending or patronizing
- elegant and dignified but not prudish
- clean, natural, uninhibited

Design specs:
- See attached file for packaging specs

Colors:
- refer to www.warrabee.com to see other products in the range. This is a guide only. Use of those colors is not mandatory.

Ingredients:

100% Macadamia Oil

Additional features:

- edible
- vegan
- gluten-free
- low allergen
- naturally anti-microbial and anti-inflammatory

See http://thebarealchemist.com/benefits-of-macadamia-nut-oil-in-skin-care/ for a list of the benefits of macadamia oil.

Target Market(s)

Our target market are the early adopters within the baby boomer set. Their age is a badge of honor, they are comfortable in their own skin and as sensual and fun-loving as ever. They are in their prime - still cool, still curious, still a little crazy. They are open to new possibilities, just as they have been at every age and stage. They still have plenty to do and plenty to enjoy. Being pre-menopausal or menopausal, natural lubrication may be diminishing. Warrabee Silk is the completely natural way to bring back the pleasure in sex.

Requirements
Must have
• Brandname: Warrabee Silk

Container Packaging specs: http://www.kestrelvessel.com/images/art/4837K15-R-ELM-STAMPED.PDF
Dispenser: http://www.kestrelvessel.com/lotion-dispenser-pumps/p/xTQ720M/
Should not have
• No post-coital pictures
No people
Nothing phallic

```html
<!DOCTYPE html>
<html lang="en">
<head>
<meta charset="utf-8">
<title>Warrabee Silk – Strawberry Label</title>
<link rel="stylesheet" href="https://fonts.googleapis.com/css2?family=Tinos:wght@400;700&family=Alex+Brush&display=swap">
<style>
  :root {
    --backdrop: #ecebe8;
    --label: #fbfaf6;
    --berry: #d0303f;
    --leaf: #9dbb3a;
    --leaf-soft: #dfe8c0;
    --ink-shadow: rgba(60, 40, 40, 0.12);
  }
  * { box-sizing: border-box; margin: 0; padding: 0; }
  html, body {
    width: 1200px;
    height: 1000px;
    overflow: hidden;
    background: var(--backdrop);
  }
  .canvas {
    position: relative;
    width: 1200px;
    height: 1000px;
    display: flex;
    align-items: center;
    justify-content: center;
  }
  .label {
    position: relative;
    width: 560px;
    height: 820px;
    background: var(--label);
    box-shadow: 0 10px 30px var(--ink-shadow);
    display: flex;
    flex-direction: column;
    align-items: center;
    overflow: hidden;
  }
  .band {
    position: absolute;
    left: 0;
    width: 100%;
  }
  .band--top { top: 0; }
  .band--bottom { bottom: 0; }
  .band .stripe-leaf { height: 8px; background: var(--leaf); }
  .band .stripe-gap { height: 5px; background: var(--label); }
  .band .stripe-berry { height: 16px; background: var(--berry); }

  .leaf-sweep {
    position: absolute;
    inset: 60px 0 60px 0;
    background: radial-gradient(ellipse 70% 55% at 40% 60%, var(--leaf-soft) 0%, rgba(223,232,192,0.35) 45%, rgba(251,250,246,0) 75%);
    opacity: 0.7;
  }

  .content {
    position: relative;
    margin-top: 90px;
    display: flex;
    flex-direction: column;
    align-items: center;
    text-align: center;
    color: var(--berry);
    font-family: "Tinos", "Times New Roman", serif;
  }
  .brand-mark {
    width: 150px;
    height: 150px;
    border-radius: 50%;
    border: 5px solid var(--berry);
  }
  .brand-name {
    margin-top: 26px;
    font-size: 74px;
    font-weight: 700;
    letter-spacing: 1px;
    line-height: 1;
  }
  .product-name {
    margin-top: 6px;
    font-family: "Alex Brush", cursive;
    font-size: 92px;
    color: var(--leaf);
    line-height: 1;
  }
  .claim {
    margin-top: 18px;
    font-size: 42px;
    line-height: 1;
  }
  .category {
    font-size: 32px;
    line-height: 1.2;
  }
  .flavour {
    margin-top: 24px;
    font-family: "Alex Brush", cursive;
    font-size: 72px;
    line-height: 1;
  }
  .ingredient {
    margin-top: 34px;
    font-size: 20px;
    letter-spacing: 0.5px;
  }
  .volume {
    margin-top: 8px;
    font-size: 22px;
  }
</style>
</head>
<body>
  <main class="canvas">
    <section class="label">
      <div class="band band--top">
        <div class="stripe-leaf"></div>
        <div class="stripe-gap"></div>
        <div class="stripe-berry"></div>
      </div>

      <div class="leaf-sweep" role="img" aria-label="Soft sweeping green leaf strokes behind the label text"></div>

      <div class="content">
        <div class="brand-mark"></div>
        <h1 class="brand-name">Warrabee</h1>
        <p class="product-name">Silk</p>
        <p class="claim">PURE &amp; NATURAL</p>
        <p class="category">Personal lubricant</p>
        <p class="flavour">strawberry</p>
        <p class="ingredient">100% MACADAMIA OIL</p>
        <p class="volume">8 oz 236.5ml</p>
      </div>

      <div class="band band--bottom">
        <div class="stripe-berry"></div>
        <div class="stripe-gap"></div>
        <div class="stripe-leaf"></div>
      </div>
    </section>
  </main>
</body>
</html>
```